Business Card Design

We are a residential half way house for the addict ,the alcoholic and dual diagnosed in recovery.
i house both men and woman age 18+

Industry/Entity Type

Residential

```html
<!DOCTYPE html>
<html lang="en">
<head>
<meta charset="utf-8">
<title>Maribel's Family Sober House – Business Card</title>
<link href="https://fonts.googleapis.com/css2?family=Oswald:wght@700&family=Roboto+Condensed:wght@300;400&display=swap" rel="stylesheet">
<style>
  :root {
    --backdrop: #e4e2df;
    --card-black: #0b0b0b;
    --card-black-soft: #1c1c1c;
    --strip-white: #f4f4f4;
    --strip-grey: #d9d9d9;
    --ink-white: #ffffff;
    --ink-muted: #e6e6e6;
    --icon-red: #c8202f;
    --frame: #111111;
    --grill-a: #7a3a1c; --grill-b: #2a1a14;
    --canoe-a: #9bb58a; --canoe-b: #c8544a;
    --fire-a: #e2541a; --fire-b: #1a0804;
  }
  * { box-sizing: border-box; margin: 0; padding: 0; }
  html, body { width: 1200px; height: 892px; overflow: hidden; background: var(--backdrop); }
  .stage { width: 1200px; height: 892px; display: flex; align-items: center; justify-content: center; }

  .card {
    position: relative; width: 1000px; height: 572px;
    background: radial-gradient(ellipse at 30% 30%, var(--card-black-soft), var(--card-black) 70%);
    box-shadow: 0 14px 40px rgba(0,0,0,.35);
    overflow: hidden;
    font-family: "Roboto Condensed", sans-serif; color: var(--ink-white);
  }

  .brand { position: absolute; left: 48px; top: 56px; font-family: "Oswald", sans-serif; font-weight: 700; line-height: .98; }
  .brand-first { font-size: 70px; letter-spacing: .5px; }
  .brand-rest { font-size: 48px; }

  .phones { position: absolute; left: 48px; top: 228px; list-style: none; }
  .phones li, .contact li { display: flex; align-items: center; gap: 12px; font-size: 24px; font-weight: 400; line-height: 34px; }

  .owner { position: absolute; right: 48px; top: 48px; text-align: right; }
  .owner-name { font-size: 60px; font-weight: 400; line-height: 1; }
  .owner-role { font-size: 20px; margin-top: 4px; }
  .owner-note { font-size: 20px; color: var(--ink-muted); }

  .contact { position: absolute; right: 48px; top: 236px; list-style: none; }
  .contact li { justify-content: flex-end; }

  .icon { width: 22px; height: 22px; flex: none; }

  .photo-strip {
    position: absolute; left: 0; bottom: 0; width: 100%; height: 212px;
    background: linear-gradient(180deg, var(--strip-white), var(--strip-grey));
    display: flex; justify-content: space-between; padding: 20px 40px;
  }
  .photo { width: 284px; height: 172px; border: 5px solid var(--frame); }
  .photo-grill { background: radial-gradient(circle at 50% 45%, var(--grill-a), var(--grill-b)); }
  .photo-canoe { background: linear-gradient(160deg, var(--canoe-a) 55%, var(--canoe-b)); }
  .photo-fire  { background: radial-gradient(circle at 45% 55%, var(--fire-a), var(--fire-b) 75%); }
</style>
</head>
<body>
<div class="stage">
  <section class="card">
    <h1 class="brand">
      <span class="brand-first">Maribel's</span><br>
      <span class="brand-rest">Family Sober House Inc</span>
    </h1>

    <ul class="phones">
      <li><svg class="icon" viewBox="0 0 22 22"><rect width="22" height="22" rx="4" fill="#fff"/><path d="M6 5l3 0 1 4-2 1a8 8 0 0 0 4 4l1-2 4 1v3a2 2 0 0 1-2 1A11 11 0 0 1 5 7a2 2 0 0 1 1-2z" fill="var(--icon-red)"/></svg>(555) 210-0481</li>
      <li><svg class="icon" viewBox="0 0 22 22"><rect width="22" height="22" rx="4" fill="#fff"/><path d="M6 5l3 0 1 4-2 1a8 8 0 0 0 4 4l1-2 4 1v3a2 2 0 0 1-2 1A11 11 0 0 1 5 7a2 2 0 0 1 1-2z" fill="var(--icon-red)"/></svg>(555) 210-0482</li>
      <li><svg class="icon" viewBox="0 0 22 22"><rect width="22" height="22" rx="4" fill="#fff"/><rect x="7" y="4" width="8" height="5" fill="var(--icon-red)"/><rect x="4" y="9" width="14" height="7" rx="1" fill="var(--icon-red)"/><rect x="7" y="14" width="8" height="4" fill="#fff" stroke="var(--icon-red)"/></svg>(555) 374-9120</li>
    </ul>

    <div class="owner">
      <p class="owner-name">Dana Whitfield</p>
      <p class="owner-role">Owner</p>
      <p class="owner-note">(15 yrs.in recovery)</p>
    </div>

    <ul class="contact">
      <li>dana.whitfield@example.com<svg class="icon" viewBox="0 0 22 22"><rect width="22" height="22" rx="4" fill="#fff"/><rect x="4" y="6" width="14" height="10" fill="var(--icon-red)"/><path d="M4 6l7 6 7-6" fill="none" stroke="#fff" stroke-width="1.5"/></svg></li>
      <li>1820 Palm Grove Rd. Harbor Vale,Fla 30000<svg class="icon" viewBox="0 0 22 22"><rect width="22" height="22" rx="4" fill="#fff"/><path d="M11 4a5 5 0 0 1 5 5c0 4-5 9-5 9s-5-5-5-9a5 5 0 0 1 5-5z" fill="var(--icon-red)"/><circle cx="11" cy="9" r="2" fill="#fff"/></svg></li>
    </ul>

    <div class="photo-strip">
      <div class="photo photo-grill" role="img" aria-label="Photo of meats and vegetable skewers on a barbecue grill"></div>
      <div class="photo photo-canoe" role="img" aria-label="Photo of a family paddling a red canoe on a lake"></div>
      <div class="photo photo-fire" role="img" aria-label="Photo of silhouetted people beside a glowing bonfire at night"></div>
    </div>
  </section>
</div>
</body>
</html>
```